Website Development for vaultmerrow.com.au

Build a new Wordpress/Responsive website for vaultmerrow.com.au

Target Market(s)

Compliance Managers, Risk Managers, Information Security and Cyber Security Professionals, Chief Data/Digital Officers, Chief Operating/Financial Officers, Business Continuity Professionals, Disaster Recovery Planners, Small Business Owners, Local/Federal Government entities

Industry/Entity Type

Data Service

Coding

Coded - Design and coding required

Number of Pages Required

5+ page

Font styles to use
Sans Serif

Colors

Designer to choose colors to be used in the design.

Requirements
Must have
• 1. Site Structure: Home Page plus the following chapter-pages for a) Services b) About c) Resources d) Blog e) Contact Us
• 2. Prefer site to built on wordpress and we can purchase a theme if needed (we currently use Kelp9 for other sites)
• 3. Blog needs to be wordpress based
• 4. We will host the site ourselves on our own servers
• 5. Responsive Design
Nice to have
• 1. Livechat capability/interface
• 2. Capability for marketing automation integration (such as hubspot, marketo, infusionsoft etc)
• 3. Capability for CRM integration (Salesforce)

```html
<!DOCTYPE html>
<html lang="en">
<head>
<meta charset="utf-8">
<title>Vaultmerrow – Visualizing Data To Build Climate Resilience</title>
<link href="https://fonts.googleapis.com/css2?family=Roboto:wght@300;400;500;700&family=Open+Sans:wght@400;600&display=swap" rel="stylesheet">
<style>
:root{
  --blue:#1565c0;
  --blue-dark:#0d3f86;
  --blue-deep:#0a2a5c;
  --sky:#e8f1fb;
  --ink:#1d1d1d;
  --text:#555;
  --muted:#8a8a8a;
  --line:#d8dde4;
  --white:#fff;
  --black:#0b0b0b;
  --grey:#7d7d7d;
}
*{margin:0;padding:0;box-sizing:border-box}
html,body{width:1200px;height:4306px;overflow:hidden}
body{position:relative;font-family:"Open Sans",Arial,sans-serif;color:var(--text);background:var(--white)}
.abs{position:absolute}
h2{font-family:"Roboto",Arial,sans-serif;font-weight:500;color:var(--ink);text-align:center}

/* top bar */
.topbar{left:0;top:0;width:1200px;height:57px;background:var(--blue-dark);color:var(--white);font-size:15px}
.topbar .contact{left:143px;top:18px;display:flex;gap:28px}
.topbar .contact span::before{content:"";display:inline-block;width:12px;height:12px;border-radius:50%;background:#7fb1ec;margin-right:8px;vertical-align:-1px}
.topbar .follow{right:90px;top:16px;display:flex;align-items:center;gap:6px;font-weight:600}
.topbar .follow i{width:22px;height:22px;display:inline-block;border-radius:3px}

/* nav */
.nav{left:0;top:57px;width:1200px;height:81px;background:var(--white)}
.brand{font-family:"Roboto",Arial,sans-serif;font-weight:700;color:var(--blue);display:flex;align-items:center;gap:10px}
.brand i{display:inline-block;border-radius:50%;background:var(--blue)}
.nav .brand{left:143px;top:22px;font-size:32px}
.nav .brand i{width:30px;height:30px}
.menu{right:150px;top:30px;display:flex;gap:34px;font-family:"Roboto",Arial,sans-serif;font-size:14px;color:#333}
.menu .on{color:var(--blue);border-bottom:3px solid var(--blue);padding-bottom:10px}

/* hero */
.hero{left:0;top:138px;width:1200px;height:465px;background:radial-gradient(ellipse at 55% 35%,#6fb4f0 0%,#2c6fc4 35%,#0d2f6e 75%,#061838 100%)}
.hero h1{left:0;top:355px;width:1200px;text-align:center;font-family:"Roboto",Arial,sans-serif;font-weight:500;font-size:36px;color:var(--white)}
.hero .dots{left:570px;top:428px;display:flex;gap:12px}
.hero .dots i{width:22px;height:4px;background:rgba(255,255,255,.5)}
.hero .dots i:first-child{background:var(--white)}

/* about */
.about-photo{left:143px;top:683px;width:446px;height:451px;background:linear-gradient(160deg,#e9edf1,#b9c3cd 60%,#5e6b78)}
.about-body{left:630px;top:720px;width:430px;font-size:13px;line-height:21px}
.about-body .title{display:flex;align-items:center;gap:16px;margin-bottom:30px}
.about-body .title h3{font-family:"Roboto",Arial,sans-serif;font-weight:500;font-size:32px;color:#444}
.about-body .title .brand{font-size:30px}
.about-body .title .brand i{width:26px;height:26px}
.about-body p{margin-bottom:14px}
.about-body b{color:var(--blue)}
.about-body .cta{color:var(--ink);font-weight:600;font-size:14px}
.about-body .cta a{color:var(--blue);font-weight:400;text-decoration:none}

/* services */
.services{left:0;top:1206px;width:1200px;height:588px;background:var(--sky);overflow:hidden}
.services h2{left:0;top:70px;width:1200px;font-size:40px}
.lead{width:1200px;left:0;text-align:center;font-size:13px;line-height:22px}
.services .lead{top:135px}
.lead b{color:var(--blue);font-weight:400}
.arc{left:327px;top:265px;width:546px;height:546px;border-radius:50%;background:#f3f8fe;border:1px solid #dbe7f5}
.core{left:428px;top:344px;width:344px;height:344px;border-radius:50%;background:var(--blue);border:8px solid #d3e4f7}
.core .brand{position:absolute;left:0;top:70px;width:328px;justify-content:center;color:var(--white);font-size:44px}
.core .brand i{background:var(--white);width:34px;height:34px}
.node{width:104px;height:104px;border-radius:50%;background:var(--white);border:6px solid #555}
.node.blue{border-color:var(--blue)}
.node svg{position:absolute;left:26px;top:26px}
.svc-label{font-family:"Roboto",Arial,sans-serif;font-size:17px;line-height:22px;color:#333}
.svc-label.blue{color:var(--blue)}

/* audience */
.audience h2{left:0;top:1895px;width:1200px;font-size:40px}
.audience .lead{top:1952px}
.aud{width:144px;height:144px;border-radius:50%;background:var(--white);border:2px solid #e4e4e4;box-shadow:0 4px 14px rgba(0,0,0,.08)}
.aud.on{border:6px solid var(--blue)}
.aud svg{position:absolute;left:44px;top:44px}
.aud-label{width:200px;text-align:center;font-family:"Roboto",Arial,sans-serif;font-size:18px;line-height:22px;color:#444}
.aud-label.on{color:var(--blue)}
.arrow{width:36px;height:36px;border-radius:50%;background:var(--white);box-shadow:0 2px 6px rgba(0,0,0,.2)}
.arrow svg{position:absolute;left:12px;top:11px}

/* team */
.team{left:0;top:2297px;width:1200px;height:718px;background:linear-gradient(180deg,#1259ad,#0d4590);overflow:hidden}
.team .slant{left:0;top:0;width:1200px;height:60px}
.team h2{left:0;top:140px;width:1200px;font-size:40px;color:var(--white)}
.team .sub{left:0;top:192px;width:1200px;text-align:center;font-size:22px;color:#cfe0f6;font-family:"Roboto",Arial,sans-serif}
.card{top:250px;width:176px;height:376px;background:var(--white);padding:12px}
.card .inner{position:absolute;inset:12px;border:1px solid var(--line)}
.card .photo{position:absolute;left:14px;top:24px;width:146px;height:200px;background:linear-gradient(170deg,#dfe3e7,#9aa6b2 70%,#5a6572)}
.card .name{position:absolute;left:0;top:255px;width:176px;text-align:center;font-family:"Roboto",Arial,sans-serif;font-size:17px;color:#333}
.card .name.on{color:var(--blue)}
.card .role{position:absolute;left:0;top:282px;width:176px;text-align:center;font-size:13px;color:var(--muted)}
.card .social{position:absolute;left:0;top:310px;width:176px;display:flex;justify-content:center;gap:8px}
.card .social i{width:9px;height:9px;border-radius:50%;background:#777}

/* blog */
.blog{left:0;top:3015px;width:1200px;height:645px;background:var(--sky);overflow:hidden}
.blog h2{left:0;top:70px;width:1200px;font-size:40px}
.post{top:200px;width:440px;height:273px;background:var(--white);border-bottom:8px solid var(--blue);box-shadow:0 2px 10px rgba(0,0,0,.06)}
.date{top:-50px;left:157px;width:126px;height:126px;border-radius:50%;background:var(--white);border:8px solid #9aa3ad;text-align:center;padding-top:16px}
.date b{display:block;font-family:"Roboto",Arial,sans-serif;font-size:44px;font-weight:500;color:var(--blue);line-height:46px}
.date span{display:inline-block;margin-top:4px;background:var(--blue);color:var(--white);font-size:13px;padding:1px 8px;border-radius:3px}
.post h4{position:absolute;left:0;top:94px;width:440px;text-align:center;font-family:"Roboto",Arial,sans-serif;font-weight:500;font-size:17px;color:var(--ink)}
.post p{position:absolute;left:50px;top:130px;width:340px;text-align:center;font-size:12.5px;line-height:19px}
.post a{position:absolute;left:0;top:228px;width:440px;text-align:center;font-size:13px;color:var(--blue)}
.btn-outline{left:525px;top:523px;width:150px;height:40px;border:1px solid var(--blue);color:var(--blue);background:var(--white);text-align:center;line-height:38px;font-size:15px}

/* start */
.start{left:0;top:3600px;width:1200px;height:534px;background:linear-gradient(180deg,#1a63bb,#0e4a96);overflow:hidden}
.start .slant{left:0;top:0;width:1200px;height:120px}
.start h2{left:0;top:160px;width:1200px;font-size:40px;color:var(--white)}
.form{left:310px;top:247px;width:646px;height:143px;border:1px solid rgba(255,255,255,.3);display:grid;grid-template-columns:1fr 1fr}
.form .fields{border-right:1px solid rgba(255,255,255,.3)}
.form .f{height:47px;border-bottom:1px solid rgba(255,255,255,.3);padding:12px 16px;font-size:13px;color:rgba(255,255,255,.75)}
.form .f:last-child{border-bottom:0}
.form .msg{padding:12px 16px;font-size:13px;color:rgba(255,255,255,.75)}
.submit{left:525px;top:425px;width:150px;height:40px;background:var(--black);color:var(--white);text-align:center;line-height:40px;font-weight:600;font-size:15px}
.chat{left:1014px;top:4102px;width:60px;height:60px;border-radius:50%;background:var(--white);box-shadow:0 2px 8px rgba(0,0,0,.3)}
.chat svg{position:absolute;left:16px;top:17px}

/* footer */
.footer{left:0;top:4134px;width:1200px;height:172px;background:var(--black);color:var(--white)}
.footer .brand{left:143px;top:44px;color:var(--white);font-size:34px}
.footer .brand i{background:var(--white);width:30px;height:30px}
.footer .links{right:150px;top:70px;display:flex;gap:34px;font-family:"Roboto",Arial,sans-serif;font-size:13px}
.footer .copy{left:143px;top:142px;font-size:11px;color:#bbb}
.footer .legal{right:150px;top:142px;font-size:11px;color:#bbb}
</style>
</head>
<body>

<header>
  <div class="abs topbar">
    <div class="abs contact"><span>+012-555-019</span><span>info@vaultmerrow.com.au</span></div>
    <div class="abs follow">Follow Us on
      <i style="background:#d9473b"></i><i style="background:#1da1f2"></i><i style="background:#2a72b5"></i><i style="background:#e02424"></i>
    </div>
  </div>
  <nav class="abs nav">
    <div class="abs brand"><i></i>Vaultmerrow</div>
    <div class="abs menu"><span class="on">HOME</span><span>ABOUT</span><span>SERVICES</span><span>RESOURCES</span><span>BLOG</span><span>CONTACT US</span></div>
  </nav>
</header>

<section class="abs hero" role="img" aria-label="Glowing digital cloud over circuit lines in deep blue">
  <h1 class="abs">Visualizing Data To Build Climate Resilience</h1>
  <div class="abs dots"><i></i><i></i></div>
</section>

<section class="about">
  <div class="abs about-photo" role="img" aria-label="Smiling businessman in a suit working on a laptop"></div>
  <div class="abs about-body">
    <div class="title"><h3>About</h3><div class="brand"><i></i>Vaultmerrow</div></div>
    <p><b>Vaultmerrow</b> It is a long established fact that a reader will be distracted by the readable content of a page when looking at its layout. The point of using Lorem Ipsum is that it has a more-or-less normal distribution.</p>
    <p>The point of using Lorem Ipsum is that it has a more-or-less normal distribution of letters, as opposed to using 'Content here, content here', making it look like readable English.</p>
    <p>Lorem Ipsum is that it has a more-or-less normal distribution of letters, as opposed to using 'Content here, content here', making it look like readable English has a more-or-less normal.</p>
    <p>The point of using Lorem Ipsum is that it has a more-or-less normal distribution of letters, as opposed to using 'Content here, content here', making it look like readable English.</p>
    <p class="cta">Get the support you need now. <a>Contact our 24/7 support line to get started.</a></p>
  </div>
</section>

<section class="abs services">
  <h2 class="abs">SERVICES</h2>
  <div class="abs lead"><b>Vaultmerrow</b> It is a long established fact that a reader will be distracted by the readable content of a page when looking at its layout.<br>The point of using Lorem Ipsum is that it has a more-or-less normal distribution of letters<br><br>The point of using Lorem Ipsum is that it has a more-or-less <b>Vaultmerrow</b> normal distribution of letters, as opposed to using<br>'Content here, content here', making it look like readable English</div>
  <div class="abs arc"></div>
  <div class="abs core"><div class="brand"><i></i>Vaultmerrow</div></div>

  <div class="abs node blue" style="left:450px;top:255px"><svg width="40" height="40" viewBox="0 0 40 40" fill="none" stroke="#1565c0" stroke-width="2.5"><rect x="6" y="8" width="28" height="20" rx="2"/><path d="M14 34h12M20 28v6"/></svg></div>
  <div class="abs svc-label blue" style="left:270px;top:278px;width:160px;text-align:right">Data Management<br>Platforms</div>

  <div class="abs node" style="left:637px;top:255px"><svg width="40" height="40" viewBox="0 0 40 40" fill="none" stroke="#555" stroke-width="2.5"><circle cx="20" cy="20" r="8"/><path d="M20 4v6M20 30v6M4 20h6M30 20h6M9 9l4 4M27 27l4 4M9 31l4-4M27 13l4-4"/></svg></div>
  <div class="abs svc-label" style="left:770px;top:280px">Industry Solutions</div>

  <div class="abs node" style="left:313px;top:384px"><svg width="40" height="40" viewBox="0 0 40 40" fill="none" stroke="#555" stroke-width="2.5"><ellipse cx="20" cy="9" rx="12" ry="4"/><path d="M8 9v22c0 2 5 4 12 4s12-2 12-4V9M8 20c0 2 5 4 12 4s12-2 12-4"/></svg></div>
  <div class="abs svc-label" style="left:120px;top:406px;width:175px;text-align:right">Data Management<br>Services</div>

  <div class="abs node" style="left:781px;top:384px"><svg width="40" height="40" viewBox="0 0 40 40" fill="none" stroke="#555" stroke-width="2.5"><path d="M20 4l13 5v10c0 9-6 14-13 17C13 33 7 28 7 19V9z"/><path d="M14 20l4 4 8-8"/></svg></div>
  <div class="abs svc-label" style="left:897px;top:406px">Ransomware<br>Protection</div>
</section>

<section class="audience">
  <h2 class="abs">TO WHOM WE SERVE</h2>
  <div class="abs lead">The point of using Lorem Ipsum is that it has a more-or-less normal distribution of letters, as opposed to using 'Content here,<br>content here', making it look like readable English</div>
  <div class="abs arrow" style="left:74px;top:2078px"><svg width="12" height="14" viewBox="0 0 12 14"><path d="M9 1L3 7l6 6" fill="none" stroke="#888" stroke-width="2"/></svg></div>
  <div class="abs arrow" style="left:1093px;top:2078px"><svg width="12" height="14" viewBox="0 0 12 14"><path d="M3 1l6 6-6 6" fill="none" stroke="#888" stroke-width="2"/></svg></div>

  <div class="abs aud" style="left:143px;top:2024px"><svg width="56" height="56" viewBox="0 0 56 56" fill="none" stroke="#666" stroke-width="2.5"><path d="M28 6L4 48h48z"/><path d="M28 22v12M28 40v2"/></svg></div>
  <div class="abs aud-label" style="left:115px;top:2200px">Risk Managers</div>

  <div class="abs aud" style="left:333px;top:2024px"><svg width="56" height="56" viewBox="0 0 56 56" fill="none" stroke="#666" stroke-width="2.5"><path d="M28 4l20 8v14c0 13-9 21-20 26C17 47 8 39 8 26V12z"/><path d="M19 28l6 6 12-12"/></svg></div>
  <div class="abs aud-label" style="left:305px;top:2200px">Information<br>Security</div>

  <div class="abs aud on" style="left:528px;top:2024px"><svg width="56" height="56" viewBox="0 0 56 56" fill="none" stroke="#1565c0" stroke-width="2.5" style="left:38px;top:38px"><rect x="14" y="14" width="28" height="28" rx="3"/><rect x="22" y="22" width="12" height="12"/><path d="M20 4v10M28 4v10M36 4v10M20 42v10M28 42v10M36 42v10M4 20h10M4 28h10M4 36h10M42 20h10M42 28h10M42 36h10"/></svg></div>
  <div class="abs aud-label on" style="left:500px;top:2200px">Cyber Security<br>Professionals</div>

  <div class="abs aud" style="left:720px;top:2024px"><svg width="56" height="56" viewBox="0 0 56 56" fill="none" stroke="#666" stroke-width="2.5"><circle cx="28" cy="14" r="8"/><path d="M14 36h28v14H14zM28 22v14M10 50h36"/></svg></div>
  <div class="abs aud-label" style="left:692px;top:2200px">Chief Data<br>Technicians</div>

  <div class="abs aud" style="left:913px;top:2024px"><svg width="56" height="56" viewBox="0 0 56 56" fill="none" stroke="#666" stroke-width="2.5"><circle cx="28" cy="16" r="9"/><path d="M10 50c0-11 8-18 18-18s18 7 18 18z"/><path d="M28 32v10"/></svg></div>
  <div class="abs aud-label" style="left:885px;top:2200px">Digital Officers</div>
</section>

<section class="abs team">
  <svg class="abs slant" width="1200" height="60" viewBox="0 0 1200 60"><polygon points="0,0 1200,0 1200,60 220,60" fill="#fff"/><polygon points="0,0 220,60 0,60" fill="#7f7f7f"/></svg>
  <h2 class="abs">OUR TEAM</h2>
  <div class="abs sub">Our Bestest Team Members.</div>
  <div class="abs arrow" style="left:140px;top:403px"><svg width="12" height="14" viewBox="0 0 12 14"><path d="M9 1L3 7l6 6" fill="none" stroke="#555" stroke-width="2"/></svg></div>
  <div class="abs arrow" style="left:1022px;top:403px"><svg width="12" height="14" viewBox="0 0 12 14"><path d="M3 1l6 6-6 6" fill="none" stroke="#555" stroke-width="2"/></svg></div>

  <div class="abs card" style="left:192px"><div class="inner"></div><div class="photo" role="img" aria-label="Portrait of team member in casual shirt"></div><div class="name">ARLO PENN</div><div class="role">Designation Here</div><div class="social"><i></i><i></i><i></i><i></i></div></div>
  <div class="abs card" style="left:402px"><div class="inner"></div><div class="photo" role="img" aria-label="Portrait of team member in blazer"></div><div class="name on">MIRA COLT</div><div class="role">Designation Here</div><div class="social"><i></i><i></i><i></i><i></i></div></div>
  <div class="abs card" style="left:612px"><div class="inner"></div><div class="photo" role="img" aria-label="Portrait of team member in suit"></div><div class="name">RAVI DUNNE</div><div class="role">Designation Here</div><div class="social"><i></i><i></i><i></i><i></i></div></div>
  <div class="abs card" style="left:822px"><div class="inner"></div><div class="photo" role="img" aria-label="Portrait of team member with glasses"></div><div class="name">THEO MARSH</div><div class="role">Designation Here</div><div class="social"><i></i><i></i><i></i><i></i></div></div>
</section>

<section class="abs blog">
  <h2 class="abs">LATEST BLOG POSTS</h2>
  <div class="abs arrow" style="left:82px;top:317px"><svg width="12" height="14" viewBox="0 0 12 14"><path d="M9 1L3 7l6 6" fill="none" stroke="#888" stroke-width="2"/></svg></div>
  <div class="abs arrow" style="left:1082px;top:317px"><svg width="12" height="14" viewBox="0 0 12 14"><path d="M3 1l6 6-6 6" fill="none" stroke="#888" stroke-width="2"/></svg></div>

  <article class="abs post" style="left:143px">
    <div class="abs date"><b>12</b><span>Feb 2019</span></div>
    <h4>The point of using Lorem Ipsum</h4>
    <p>"The point of using Lorem Ipsum is that it has a more-or-less normal distribution of letters, as opposed to using 'Content here, content here', making it look like readable English, as opposed to using 'Content here, content here.</p>
    <a>Learn More</a>
  </article>
  <article class="abs post" style="left:617px">
    <div class="abs date"><b>06</b><span>Feb 2019</span></div>
    <h4>The point of using Lorem Ipsum</h4>
    <p>"The point of using Lorem Ipsum is that it has a more-or-less normal distribution of letters, as opposed to using 'Content here, content here', making it look like readable English letters, as opposed to using 'Content here, content here."</p>
    <a>Learn More</a>
  </article>
  <div class="abs btn-outline">View All</div>
</section>

<section class="abs start">
  <svg class="abs slant" width="1200" height="120" viewBox="0 0 1200 120"><polygon points="0,0 1200,0 1200,0 0,60" fill="#e8f1fb"/><polygon points="0,60 0,0 0,0" fill="#7f7f7f"/></svg>
  <h2 class="abs">LET'S GET STARTED</h2>
  <form class="abs form">
    <div class="fields"><div class="f">Your Name</div><div class="f">Your Email</div><div class="f">Your Contact Number</div></div>
    <div class="msg">Your Message</div>
  </form>
  <div class="abs submit">Submit</div>
</section>

<div class="abs chat"><svg width="28" height="26" viewBox="0 0 28 26"><path d="M3 3h22v15H12l-6 5v-5H3z" fill="#1565c0"/></svg></div>

<footer class="abs footer">
  <div class="abs brand"><i></i>Vaultmerrow</div>
  <div class="abs links"><span>HOME</span><span>ABOUT</span><span>SERVICES</span><span>RESOURCES</span><span>BLOG</span><span>CONTACT US</span></div>
  <div class="abs copy">Copyright 2019 @ Vaultmerrow. All Rights Reserved.</div>
  <div class="abs legal">Terms of services | Privacy Policy</div>
</footer>

</body>
</html>
```